Help our Sugar Loom find our winning design! We're looking for a business card....

We’re a Sugar Loom in NY specializing in custom-made cakes and unique desserts.
Our cakes combine flavor and art, each designed to match customer’s special event and theme.
We’d like a unique business card with a clean design that will combine French chic and artistic look & feel.
We’d like to differentiate ourselves from standard bakeries, please don’t offer cupcake images :-)
Our logo is peach-pink and brown and we’d love to use these colors ( . Another color that can be added is gold - or feel free to suggest!

Target Market(s)

Women, ages 25-55

Industry/Entity Type

Boutique

Contact Information for Business Card

Text on card:
Logo
Sugar Loom by Dana Welch

www.sugarloomsweets.com
hello@sugarloom.com
(516) 555-0147
F – sugarloomnyc
IG - sugarloom_ny

Font styles to use
Sans Serif
Script

Requirements
Must have
• Logo
• Clean look
• French chic and artistic look & feel.
Nice to have
• Damask pattern
Should not have
• Cupcake images

```html
<!DOCTYPE html>
<html lang="en">
<head>
<meta charset="utf-8">
<title>Sugar Loom – Business Card</title>
<link href="https://fonts.googleapis.com/css2?family=Montserrat:wght@400;600&family=Pinyon+Script&display=swap" rel="stylesheet">
<style>
  :root {
    --bg: #e4e4e4;
    --card: #ffffff;
    --blush-tint: #f7eeee;
    --rose: #deb0ab;
    --gold-dark: #8a6a2c;
    --gold: #b38b3e;
    --gold-light: #e9c36a;
    --cocoa: #2e2522;
    --ink: #3a3a3a;
  }
  * { margin: 0; padding: 0; box-sizing: border-box; }
  html, body { width: 1200px; height: 852px; overflow: hidden; }
  body { background: var(--bg); position: relative; font-family: "Montserrat", Arial, sans-serif; }

  .card {
    position: absolute;
    width: 520px;
    height: 300px;
    border-radius: 24px;
    overflow: hidden;
    background: var(--card);
    box-shadow: 0 10px 24px rgba(0,0,0,0.18);
  }
  .card--front { left: 100px; top: 120px; }
  .card--back  { left: 580px; top: 420px; background: linear-gradient(180deg, var(--blush-tint), var(--card) 70%); }

  .brand-name {
    font-family: "Pinyon Script", cursive;
    color: var(--cocoa);
    font-weight: 400;
    white-space: nowrap;
  }
  .card--front .brand-name {
    position: absolute; left: 0; right: 0; top: 112px;
    text-align: center; font-size: 62px; line-height: 1;
  }
  .card--back .brand-name {
    position: absolute; left: 70px; top: 64px;
    font-size: 46px; line-height: 1;
  }

  .back-art { position: absolute; inset: 0; }

  .contact-list {
    position: absolute; left: 62px; top: 166px;
    list-style: none;
  }
  .contact-item {
    display: flex; align-items: center; gap: 9px;
    font-size: 12.5px; color: var(--ink); height: 19px;
    white-space: nowrap;
  }
  .contact-icon {
    width: 13px; height: 13px; border-radius: 2px;
    background: linear-gradient(135deg, var(--gold-light), var(--gold-dark));
    display: flex; align-items: center; justify-content: center;
    flex: none;
  }
  .contact-icon svg { width: 9px; height: 9px; }

  .owner {
    position: absolute; right: 14px; top: 186px; width: 140px;
    text-align: center; color: #fff;
  }
  .owner-tagline { font-size: 12px; letter-spacing: 0.3px; white-space: nowrap; }
  .owner-name {
    font-family: "Pinyon Script", cursive;
    font-size: 28px; line-height: 1.2; white-space: nowrap;
  }
</style>
</head>
<body>

  <section class="card card--front">
    <h1 class="brand-name">Sugar Loom</h1>
  </section>

  <section class="card card--back">
    <svg class="back-art" viewBox="0 0 520 300" preserveAspectRatio="none" aria-hidden="true">
      <defs>
        <linearGradient id="goldFill" x1="0" y1="0" x2="1" y2="1">
          <stop offset="0" stop-color="#7d5f25"/>
          <stop offset="0.55" stop-color="#a9843c"/>
          <stop offset="1" stop-color="#f0c866"/>
        </linearGradient>
      </defs>
      <path d="M520 44 C430 64 385 145 335 205 C295 252 245 284 190 300 L520 300 Z" fill="url(#goldFill)"/>
      <path d="M0 292 C140 274 250 252 312 192 C362 140 420 64 520 34" fill="none" stroke="var(--rose)" stroke-width="5"/>
      <path d="M0 278 C150 264 250 246 300 212" fill="none" stroke="var(--rose)" stroke-width="2"/>
      <path d="M0 300 L0 289 C120 278 210 272 290 262 C240 282 200 293 170 300 Z" fill="var(--rose)"/>
    </svg>

    <h2 class="brand-name">Sugar Loom</h2>

    <ul class="contact-list">
      <li class="contact-item">
        <span class="contact-icon"><svg viewBox="0 0 10 10"><path d="M2 1 L4 1 L4.6 3 L3.6 3.8 C4.2 5 5 5.8 6.2 6.4 L7 5.4 L9 6 L9 8 C5 8.5 1.5 5 2 1 Z" fill="#fff"/></svg></span>
        (516) 555-0147
      </li>
      <li class="contact-item">
        <span class="contact-icon"><svg viewBox="0 0 10 10"><rect x="1" y="2.5" width="8" height="5.5" fill="#fff"/><path d="M1 2.5 L5 5.8 L9 2.5" fill="none" stroke="#a9843c" stroke-width="0.8"/></svg></span>
        hello@sugarloom.com
      </li>
      <li class="contact-item">
        <span class="contact-icon"><svg viewBox="0 0 10 10"><circle cx="5" cy="5" r="3.6" fill="none" stroke="#fff" stroke-width="1"/><path d="M1.4 5 H8.6 M5 1.4 C3 3.5 3 6.5 5 8.6 M5 1.4 C7 3.5 7 6.5 5 8.6" fill="none" stroke="#fff" stroke-width="0.7"/></svg></span>
        www.sugarloomsweets.com
      </li>
      <li class="contact-item">
        <span class="contact-icon"></span>
        \sugarloomnyc
      </li>
    </ul>

    <div class="owner">
      <p class="owner-tagline">Sugar Loom by</p>
      <p class="owner-name">Dana Welch</p>
    </div>
  </section>

</body>
</html>
```